We need a new website design for our company Brindle Forks (https://www.brindleforks.com/). We DO NOT WANT A BORING STANDARD SITE. This site has to be different, and has to POP!

Logo Files: https://files.examplecloud.net/folders/a7Kq3Lm9Zx2Tp8Rw4Vn6Yb1Hc5Jd0Fs

Website Photos here: https://files.examplecloud.net/folders/b3Wm8Qx_T2ngVr7Lp4Ks9Hd6Zc1Ya0Ej

Websites we like:
https://morvenite.sitebloom.io/
http://crunova.com/

We will need the site building Wordpress/Woocommerce and also help with interior pages & installation plug-ins -- see further attachments.

Information about the company:
1. PURPOSE: Why do we exist?
We believe that food is the root source to healthy living.
2. VISION: What future do we want to help create?
A world of healthy and happy people.
3. MISSION: What are we here to do?
Empower every person to utilize food as a means of living a healthy life.

Value Proposition:
Brindle Forks develops new food based on the latest science to provide the human body with the proper nutrients for optimal health. Our research based foods target the key health functions that support healthy aging and active lifestyles. Since 2002, we have been innovating and designing our meals to meet the needs for healthy aging to active lifestyles. To help people perform their best, today & in the future.

Objective:
This is a nationwide issue and it's coming to the surface. Food affects people in a number of different ways. Our objective is to create an approachable and sustainable solution that can assist people with a number of ailments. The end result for all of them is feeling a feeling they haven't felt in quite some time. Feeling a refreshed you. Like water for fish, food for humans. Keep it clean and simple so you can focus on enjoying your life.

PHRASES/TAGLINES:
Empowerment Through Food
Real Food, Real Results
Nutrition Made Simple
Not Just Meal Prep, Food Science
A healthier you, delivered to your door
Increase your health and wellness baseline.
Discover the potential of healthier eating
Become the best version of you
It’s incredible what proper nutrition feels like
Taste & feel the difference. Your future self will thank you.
A healthier you is just a meal away
Life Changing results
Overwhelmed with being healthy, stops here.
Designed by doctors, approved by humans
Results Driven Healthy Eating, Delivered to you.
Become the person you deserve to be.
Enjoy the process of becoming a better you

Value Propositions:
We Educate & Empower People Through Food to Live Their Best Life
Sustainable health through proper nutrition… that’s enjoyable too.

Key Statements:
We provide satisfying meals that are nutrient dense & deliver results.
Our meals provide an easy way to enjoy an anti-inflammatory diet that's as satisfying as it is healthy.
Health, fat loss & feeling good through chef-prepared, nutrient-dense, satisfying meals delivered to your door.

PLEASE REVIEW THE ATTACHMENTS.

Industry/Entity Type

See Description & Attachments

Coding

Coded - Design and coding required

Number of Pages Required

5+ page

Font styles to use
Other font styles liked:
• See Description & Attachments

Colors
0094D4
00A9DD
6FCCEA
C7EBF8
E9F6FB
00AB8E
00BBA5
67D7C9
C6EFE9
E9F9F6

Requirements
Must have
Nice to have
Should not have

```html
<!DOCTYPE html>
<html lang="en">
<head>
<meta charset="utf-8">
<title>Brindle Forks — Become The Best Version Of You</title>
<link href="https://fonts.googleapis.com/css2?family=Josefin+Sans:wght@400;600;700&family=Montserrat:wght@400;500;600;700&display=swap" rel="stylesheet">
<style>
:root{
  --forest:#0f4a36;
  --forest-deep:#0b3d2c;
  --sage:#66977b;
  --sage-light:#9cc0a3;
  --mint-bg:#e5eeec;
  --blob:#c9dccf;
  --ink:#1f2d27;
  --muted:#4a5550;
  --white:#ffffff;
  --paper:#f4f6f5;
}
*{box-sizing:border-box;margin:0;padding:0}
html,body{width:1200px;height:5396px;overflow:hidden}
body{position:relative;background:var(--white);font-family:'Montserrat',sans-serif;color:var(--ink)}
.abs{position:absolute}
.h-font{font-family:'Josefin Sans',sans-serif}
.accent{color:var(--sage-light)}
.center{text-align:center}
.btn{position:absolute;display:flex;align-items:center;gap:10px;background:var(--forest);color:var(--white);border-radius:22px;font-family:'Josefin Sans',sans-serif;font-weight:700;font-size:15px;letter-spacing:.5px;padding:0 18px 0 5px;height:38px;text-transform:uppercase}
.btn .dot{width:28px;height:28px;border-radius:50%;background:var(--white);display:flex;align-items:center;justify-content:center}
.btn.outline{box-shadow:0 0 0 2px var(--white) inset}
.marker{position:absolute;left:50%;width:14px;height:14px;margin-left:-7px;border-radius:50%;background:var(--sage)}
.photo{position:absolute}

/* top bar & header */
.topbar{top:0;left:0;width:1200px;height:42px;background:var(--forest);color:var(--white);font-size:13px;display:flex;align-items:center;justify-content:center}
.header{top:42px;left:0;width:1200px;height:110px;z-index:3}
.brand{position:absolute;font-family:'Josefin Sans',sans-serif;font-weight:700;color:var(--forest)}
.nav{position:absolute;top:86px;font-family:'Josefin Sans',sans-serif;font-size:16px;color:var(--ink)}
.nav.active{font-weight:700}
.nav.active::after{content:"";position:absolute;left:0;right:0;bottom:-7px;height:2px;background:var(--forest)}

/* hero */
.hero{top:147px;left:0;width:1200px;height:663px;background:var(--sage)}
.hero h1{position:absolute;left:111px;top:166px;font-family:'Josefin Sans',sans-serif;font-weight:700;font-size:52px;line-height:59px;letter-spacing:1.5px;color:var(--forest-deep)}
.hero p{position:absolute;left:111px;top:366px;width:460px;font-size:15px;line-height:22px;color:var(--forest-deep)}

/* generic section title */
.title{position:absolute;left:0;width:1200px;text-align:center;font-family:'Josefin Sans',sans-serif;font-weight:700;font-size:31px;letter-spacing:1px;color:var(--forest)}
.lead{position:absolute;text-align:center;font-size:13.5px;line-height:24px;color:var(--muted)}

/* features */
.features{top:1256px;left:0;width:1200px;height:508px;background:var(--mint-bg)}
.feat{position:absolute;width:240px;text-align:center}
.feat .blob{width:96px;height:94px;margin:0 auto;border-radius:46% 54% 50% 50%/55% 45% 55% 45%;background:var(--blob);display:flex;align-items:center;justify-content:center}
.feat h3{margin-top:50px;font-family:'Josefin Sans',sans-serif;font-weight:600;font-size:22px;color:var(--forest)}

/* mission */
.mission{top:1763px;left:0;width:1200px;height:482px;background:var(--forest)}
.mission h2{position:absolute;left:86px;font-family:'Josefin Sans',sans-serif;font-weight:600;font-size:29px;color:var(--white)}
.mission p{position:absolute;left:86px;width:460px;font-size:12.5px;line-height:21px;color:var(--white)}

/* menu grid */
.tile{position:absolute;width:233px;height:161px;border-radius:8px}
.tile-label{position:absolute;width:233px;text-align:center;font-family:'Josefin Sans',sans-serif;font-weight:700;font-size:18px;color:var(--forest)}

/* awards */
.awards{top:3053px;left:0;width:1200px;height:486px;background:var(--forest)}
.stat{position:absolute;width:250px;text-align:center;color:var(--white)}
.stat .ring{width:94px;height:94px;margin:0 auto;border-radius:50%;border:2px solid var(--white);display:flex;align-items:center;justify-content:center}
.stat .num{margin-top:18px;font-family:'Josefin Sans',sans-serif;font-weight:700;font-size:40px;line-height:46px}
.stat .lbl{font-family:'Josefin Sans',sans-serif;font-weight:600;font-size:19px;line-height:24px}

/* audience cards */
.card{position:absolute;width:312px;height:485px;background:var(--white);box-shadow:0 4px 18px rgba(0,0,0,.12)}
.card .img{position:absolute;left:0;top:0;width:312px;height:250px}
.card .badge{position:absolute;left:114px;top:188px;width:84px;height:84px;border-radius:50%;background:var(--forest);border:4px solid var(--white);display:flex;align-items:center;justify-content:center}
.card h3{position:absolute;top:298px;width:100%;text-align:center;font-family:'Josefin Sans',sans-serif;font-weight:700;font-size:22px;letter-spacing:1px;color:var(--forest)}
.card p{position:absolute;top:336px;left:20px;width:272px;text-align:center;font-size:12.5px;line-height:19px;color:var(--muted)}
.card .btn{left:66px;top:402px;height:38px}
.arrow{position:absolute;width:26px;height:26px;border-radius:50%;background:var(--forest);display:flex;align-items:center;justify-content:center}

/* enjoy */
.enjoy-box{position:absolute;left:519px;top:4349px;width:668px;height:419px;background:var(--white);border:2px solid var(--sage-light)}
.enjoy-box h2{position:absolute;left:50px;top:42px;font-family:'Josefin Sans',sans-serif;font-weight:700;font-size:28px;line-height:34px;letter-spacing:1px;color:var(--forest)}
.enjoy-box h4{position:absolute;left:50px;display:flex;align-items:center;gap:12px;font-family:'Josefin Sans',sans-serif;font-weight:700;font-size:19px;color:var(--forest)}
.enjoy-box p{position:absolute;left:58px;width:570px;font-size:12.5px;line-height:24px;color:var(--muted)}

/* footer */
.footer{top:4800px;left:0;width:1200px;height:596px;background:var(--paper)}
.fcol{position:absolute;top:5040px;font-size:13.5px;color:var(--ink)}
.fcol h5{font-family:'Josefin Sans',sans-serif;font-weight:600;font-size:18px;margin-bottom:14px;color:var(--ink)}
.fcol li{list-style:none;line-height:31px}
.contact{display:flex;gap:14px;align-items:flex-start;margin-bottom:14px;line-height:20px}
.contact .ic{flex:none;width:26px;height:26px;border-radius:50%;background:var(--forest);display:flex;align-items:center;justify-content:center}
.social{display:inline-block;width:26px;height:26px;border-radius:50%;background:var(--forest);margin-right:6px}
</style>
</head>
<body>

<div class="abs topbar">Become The Best Version Of You!</div>

<!-- header -->
<svg class="abs header" width="1200" height="110" viewBox="0 0 1200 110" aria-hidden="true">
  <path d="M0 0H1200V96C1050 110 960 86 800 98C620 112 520 92 340 104C200 112 90 92 0 100Z" fill="#fff"/>
</svg>
<div class="brand" style="top:80px;left:108px;font-size:21px;z-index:4">Brindle Forks</div>
<div class="nav active" style="left:312px;z-index:4">Home</div>
<div class="nav" style="left:394px;z-index:4">Shop Now</div>
<div class="nav" style="left:509px;z-index:4">About</div>
<div class="nav" style="left:591px;z-index:4">Menu</div>
<div class="nav" style="left:666px;z-index:4">Programs</div>
<div class="nav" style="left:775px;z-index:4">FAQ</div>
<svg class="abs" style="left:848px;top:80px;z-index:4" width="28" height="28" viewBox="0 0 28 28" aria-label="Search"><circle cx="14" cy="14" r="14" fill="#0f4a36"/><circle cx="12.5" cy="12.5" r="5" fill="none" stroke="#fff" stroke-width="2"/><path d="M16 16l5 5" stroke="#fff" stroke-width="2"/></svg>
<svg class="abs" style="left:899px;top:76px;z-index:4" width="34" height="32" viewBox="0 0 34 32" aria-label="Cart"><circle cx="14" cy="18" r="14" fill="#0f4a36"/><path d="M9 15h10l-1 9h-8z" fill="#fff"/><path d="M11 15a3 3 0 0 1 6 0" fill="none" stroke="#fff" stroke-width="1.5"/><circle cx="26" cy="7" r="6" fill="#66977b"/><text x="26" y="10" font-size="8" text-anchor="middle" fill="#fff" font-family="Montserrat">0</text></svg>
<div class="btn outline" style="left:974px;top:75px;height:42px;width:122px;z-index:4;border:2px solid var(--forest);box-shadow:none"><span class="dot"><svg width="14" height="14" viewBox="0 0 14 14"><path d="M2 7l3 3 7-7" fill="none" stroke="#0f4a36" stroke-width="2"/></svg></span>Log In</div>

<!-- hero -->
<section class="abs hero">
  <h1>It’s Incredible What<br>Proper Nutrition<br>Feels Like</h1>
  <p>As We Already Know, If You Are Not Currently Living A Healthy Lifestyle, Becoming Healthy Is Not Something That Happens Overnight.</p>
  <div class="btn outline" style="left:111px;top:448px;width:160px"><span class="dot"><svg width="14" height="14" viewBox="0 0 14 14"><path d="M2 7l3 3 7-7" fill="none" stroke="#0f4a36" stroke-width="2"/></svg></span>Shop Now</div>
  <div class="photo" role="img" aria-label="Two cupped hands holding a wooden bowl of broccoli, tomato and almonds" style="left:775px;top:136px;width:366px;height:471px;border-radius:48% 48% 30% 30%;background:radial-gradient(ellipse at 50% 35%,#7a4a2c 0%,#a8673f 28%,#d9a98a 55%,rgba(217,169,138,0) 75%)"></div>
  <svg class="abs" style="left:0;bottom:-1px" width="1200" height="40" viewBox="0 0 1200 40" aria-hidden="true"><path d="M0 20C150 0 300 36 480 18C660 0 820 34 1000 16C1100 6 1160 14 1200 20V40H0Z" fill="#fff"/></svg>
</section>

<!-- welcome -->
<div class="marker" style="top:900px"></div>
<div class="title" style="top:932px">Welcome To <span class="accent">Brindle Forks</span></div>
<p class="lead" style="left:126px;top:986px;width:950px">We Are Proud To Say That Brindle Forks Is Much More Than A Healthy Food, Home And Business Delivery Service. Combined With Our Network Of Highly Qualified And Experienced Health, Wellness And Fitness Professionals, Brindle Forks Is Your Food, Exercise, &amp; Science Based Wellness System!</p>
<p class="lead" style="left:126px;top:1068px;width:950px">There Are Many Reasons Why The Brindle Forks Is The Most Convenient Grab And Go Healthy Meals Home And Business Food Delivery And Complete Wellness Program, Out There Today!</p>
<div class="btn" style="left:517px;top:1137px;width:166px"><span class="dot"><svg width="14" height="14" viewBox="0 0 14 14"><path d="M2 7l3 3 7-7" fill="none" stroke="#0f4a36" stroke-width="2"/></svg></span>Read More</div>

<!-- features -->
<section class="abs features">
  <div class="marker" style="top:80px"></div>
  <div class="title" style="top:104px">Science Backed, Chef Prepared Meals… <span class="accent">Delivered Fresh</span></div>
  <p class="lead" style="left:126px;top:150px;width:950px">More than just a meal plan, we provide a sustainable diet &amp; nutritional support that empowers you to live your best life, no matter your health goals.</p>
  <div class="feat" style="left:58px;top:242px"><div class="blob"><svg width="46" height="46" viewBox="0 0 46 46"><circle cx="23" cy="23" r="18" fill="none" stroke="#0f4a36" stroke-width="2.5"/><path d="M23 12v22M17 18l6 5 6-5M17 25l6 5 6-5" fill="none" stroke="#0f4a36" stroke-width="2"/></svg></div><h3>Gluten Free</h3></div>
  <div class="feat" style="left:337px;top:242px"><div class="blob"><svg width="46" height="46" viewBox="0 0 46 46"><circle cx="23" cy="23" r="18" fill="none" stroke="#0f4a36" stroke-width="2.5"/><rect x="18" y="13" width="10" height="20" rx="2" fill="none" stroke="#0f4a36" stroke-width="2"/><path d="M11 11l24 24" stroke="#0f4a36" stroke-width="2.5"/></svg></div><h3>Lactose Free</h3></div>
  <div class="feat" style="left:615px;top:242px"><div class="blob"><svg width="46" height="46" viewBox="0 0 46 46"><circle cx="23" cy="23" r="18" fill="none" stroke="#0f4a36" stroke-width="2.5"/><path d="M19 13h8v4l2 3v13h-12V20l2-3z" fill="none" stroke="#0f4a36" stroke-width="2"/><path d="M11 11l24 24" stroke="#0f4a36" stroke-width="2.5"/></svg></div><h3>Dairy Free</h3></div>
  <div class="feat" style="left:894px;top:242px"><div class="blob"><svg width="46" height="46" viewBox="0 0 46 46"><circle cx="23" cy="23" r="18" fill="none" stroke="#0f4a36" stroke-width="2.5"/><rect x="15" y="17" width="12" height="12" fill="none" stroke="#0f4a36" stroke-width="2"/><path d="M11 11l24 24" stroke="#0f4a36" stroke-width="2.5"/></svg></div><h3>Sugar Free</h3></div>
</section>

<!-- mission -->
<section class="abs mission">
  <h2 style="top:100px">Our Mission:</h2>
  <p style="top:158px">Educate &amp; Empower People Through Food To Live Their Best Life.</p>
  <h2 style="top:228px">Value Propositions:</h2>
  <p style="top:286px">We Educate &amp; Empower People Through Food to Live Their Best Life.Sustainable health through proper nutrition... that’s enjoyable too.</p>
  <div class="photo" role="img" aria-label="Video still of a family sharing a meal at a dinner table" style="left:655px;top:0;width:545px;height:482px;background:linear-gradient(135deg,#4a3526 0%,#8a6a4c 45%,#c9a57d 75%,#6d4e36 100%)"></div>
  <svg class="abs" style="left:900px;top:212px" width="56" height="56" viewBox="0 0 56 56" aria-label="Play video"><circle cx="28" cy="28" r="28" fill="#fff"/><path d="M22 17l18 11-18 11z" fill="#0f4a36"/></svg>
  <svg class="abs" style="left:0;bottom:-1px" width="1200" height="24" viewBox="0 0 1200 24" aria-hidden="true"><path d="M0 12C200 0 400 22 600 10C800 0 1000 22 1200 8V24H0Z" fill="#fff"/></svg>
</section>

<!-- menu -->
<div class="marker" style="top:2344px"></div>
<div class="title" style="top:2374px">Weight Loss. Health Issues. Improved Performance.</div>
<div class="title accent" style="top:2412px">We’ve Got You.</div>
<div class="tile" role="img" aria-label="Seafood fillet with asparagus" style="left:111px;top:2467px;background:linear-gradient(135deg,#4e6b3a,#c99a5b 60%,#3e5a2e)"></div>
<div class="tile" role="img" aria-label="Chocolate snack bars" style="left:360px;top:2467px;background:linear-gradient(135deg,#d9d3cc,#5a3a28 55%,#e6e1dc)"></div>
<div class="tile" role="img" aria-label="Fruit smoothies in glasses" style="left:607px;top:2467px;background:linear-gradient(135deg,#f1f1ea,#9cc24a 40%,#f29a2e 75%,#e04a2a)"></div>
<div class="tile" role="img" aria-label="Grilled chicken slices" style="left:856px;top:2467px;background:linear-gradient(135deg,#3c3a36,#d9c6b0 50%,#6b5a46)"></div>
<div class="tile-label" style="left:111px;top:2645px">Seafood</div>
<div class="tile-label" style="left:360px;top:2645px">Snacks</div>
<div class="tile-label" style="left:607px;top:2645px">Smoothies</div>
<div class="tile-label" style="left:856px;top:2645px">Chicken</div>
<div class="tile" role="img" aria-label="Green grain salad" style="left:111px;top:2697px;background:linear-gradient(135deg,#6b2a4a,#b5c25a 35%,#9db34a 70%,#5a2a3a)"></div>
<div class="tile" role="img" aria-label="Coconut coated dessert balls" style="left:360px;top:2697px;background:linear-gradient(135deg,#e6e3de,#3a2a22 50%,#d6d1ca)"></div>
<div class="tile" role="img" aria-label="Sliced turkey on a board" style="left:607px;top:2697px;background:linear-gradient(135deg,#7a2a26,#b5503c 50%,#5a1e1a)"></div>
<div class="tile" role="img" aria-label="Breakfast dishes on a table" style="left:856px;top:2697px;background:linear-gradient(135deg,#3a2e26,#b08a62 50%,#d8c4a8)"></div>
<div class="tile-label" style="left:111px;top:2873px">Salads</div>
<div class="tile-label" style="left:360px;top:2873px">Desserts</div>
<div class="tile-label" style="left:607px;top:2873px">Turkey</div>
<div class="tile-label" style="left:856px;top:2873px">Breakfast</div>
<div class="btn" style="left:517px;top:2934px;width:166px"><span class="dot"><svg width="14" height="14" viewBox="0 0 14 14"><path d="M2 7l3 3 7-7" fill="none" stroke="#0f4a36" stroke-width="2"/></svg></span>View Menu</div>

<!-- awards -->
<section class="abs awards">
  <div class="title" style="top:100px;color:#fff">Award Winning Meals</div>
  <p class="lead" style="left:0;top:150px;width:1200px;color:#fff">Brindle Forks is just like having your own personal healthy chef. No more stress over shopping, prepping, cooking or cleaning.</p>
  <div class="stat" style="left:43px;top:213px"><div class="ring"><svg width="54" height="54" viewBox="0 0 54 54" fill="none" stroke="#fff" stroke-width="2"><circle cx="17" cy="18" r="6"/><circle cx="37" cy="18" r="6"/><circle cx="27" cy="26" r="6"/><path d="M15 46v-8a12 12 0 0 1 24 0v8"/></svg></div><div class="num">150K</div><div class="lbl">Happy Clients</div></div>
  <div class="stat" style="left:361px;top:213px"><div class="ring"><svg width="54" height="54" viewBox="0 0 54 54" fill="none" stroke="#fff" stroke-width="2"><path d="M8 36h38M12 36a15 15 0 0 1 30 0M27 14v7M20 44h14"/></svg></div><div class="num">500K</div><div class="lbl">Meals Served Nation<br>Wide</div></div>
  <div class="stat" style="left:667px;top:213px"><div class="ring"><svg width="54" height="54" viewBox="0 0 54 54" fill="none" stroke="#fff" stroke-width="2"><path d="M18 20a6 6 0 1 1 4-10 7 7 0 0 1 12 2 5 5 0 1 1 2 8z"/><path d="M20 20v8h16v-8M18 46V36h20v10"/></svg></div><div class="num">35+</div><div class="lbl">Chef Prepared Meals</div></div>
  <div class="stat" style="left:921px;top:213px"><div class="ring"><svg width="54" height="54" viewBox="0 0 54 54" fill="none" stroke="#fff" stroke-width="2"><circle cx="27" cy="22" r="12"/><circle cx="27" cy="22" r="6"/><path d="M19 32l-4 14 6-3 4 5 2-10M35 32l4 14-6-3-4 5-2-10"/></svg></div><div class="num">215</div><div class="lbl">Awards</div></div>
</section>

<!-- audience -->
<div class="marker" style="top:3600px"></div>
<div class="title" style="top:3630px">Who is <span style="color:var(--forest)">Brindle</span> <span class="accent">Forks For?</span></div>
<div class="arrow" style="left:41px;top:3943px"><svg width="10" height="10" viewBox="0 0 10 10"><path d="M7 1L3 5l4 4" fill="none" stroke="#fff" stroke-width="2"/></svg></div>
<div class="arrow" style="left:1130px;top:3943px"><svg width="10" height="10" viewBox="0 0 10 10"><path d="M3 1l4 4-4 4" fill="none" stroke="#fff" stroke-width="2"/></svg></div>

<div class="card" style="left:111px;top:3713px">
  <div class="img" role="img" aria-label="Two men smiling in a gym giving thumbs up" style="background:linear-gradient(160deg,#c9c4bc,#6a6058 55%,#2e2a26)"></div>
  <div class="badge"><svg width="44" height="30" viewBox="0 0 44 30"><path d="M2 16h10l4-10 6 18 5-12 3 4h12" fill="none" stroke="#fff" stroke-width="3"/></svg></div>
  <h3>General Health</h3>
  <p>You need the support of a healthy diet to get back in shape and improve your overall health.</p>
  <div class="btn" style="width:176px"><span class="dot"><svg width="14" height="14" viewBox="0 0 14 14"><path d="M2 7l3 3 7-7" fill="none" stroke="#0f4a36" stroke-width="2"/></svg></span>Learn More</div>
</div>
<div class="card" style="left:444px;top:3755px">
  <div class="img" role="img" aria-label="Silhouette of a person with arms raised against a sunset sky" style="background:linear-gradient(180deg,#7e97b5 0%,#c8c9c2 55%,#f2c46a 80%,#3a3a2e 100%)"></div>
  <div class="badge"><svg width="40" height="40" viewBox="0 0 40 40"><circle cx="20" cy="13" r="7" fill="#fff"/><path d="M6 36a14 14 0 0 1 28 0z" fill="#fff"/></svg></div>
  <h3>Business Individuals</h3>
  <p>You need the support of a healthy diet to get back in shape and improve your overall health.</p>
  <div class="btn" style="width:176px"><span class="dot"><svg width="14" height="14" viewBox="0 0 14 14"><path d="M2 7l3 3 7-7" fill="none" stroke="#0f4a36" stroke-width="2"/></svg></span>Learn More</div>
</div>
<div class="card" style="left:775px;top:3713px">
  <div class="img" role="img" aria-label="Two athletes giving a high five in a stadium" style="background:linear-gradient(150deg,#3a66a8,#8fb0d6 45%,#e8e4de 70%,#5a4a3e)"></div>
  <div class="badge"><svg width="40" height="40" viewBox="0 0 40 40"><path d="M10 30c2-8 8-14 16-16l4 4c-6 2-10 6-12 12z" fill="#fff"/><circle cx="14" cy="12" r="5" fill="#fff"/></svg></div>
  <h3>Fitness Enthusiasts</h3>
  <p>You need the support of a healthy diet to get back in shape and improve your overall health.</p>
  <div class="btn" style="width:176px"><span class="dot"><svg width="14" height="14" viewBox="0 0 14 14"><path d="M2 7l3 3 7-7" fill="none" stroke="#0f4a36" stroke-width="2"/></svg></span>Learn More</div>
</div>

<!-- enjoy -->
<div class="photo" role="img" aria-label="Smiling woman eating a salad from a bowl" style="left:0;top:4324px;width:601px;height:467px;clip-path:polygon(0 0,100% 0,100% 100%,6% 100%,0 90%);background:linear-gradient(120deg,#e9e3da 0%,#d9a77e 40%,#b9653c 60%,#f1ece6 85%)"></div>
<div class="enjoy-box">
  <h2>Enjoy The Process Of Becoming A<br><span class="accent">Better You!</span></h2>
  <h4 style="top:132px"><svg width="18" height="18" viewBox="0 0 18 18"><circle cx="9" cy="9" r="9" fill="#0f4a36"/><path d="M5 9l3 3 5-6" fill="none" stroke="#fff" stroke-width="2"/></svg>Fresh Meals Delivered Weekly</h4>
  <p style="top:170px">Eating properly is no longer difficult. We’ve handcrafted delicious meals that are results driven, so all you need to do is, enjoy.</p>
  <h4 style="top:242px"><svg width="18" height="18" viewBox="0 0 18 18"><circle cx="9" cy="9" r="9" fill="#0f4a36"/><path d="M5 9l3 3 5-6" fill="none" stroke="#fff" stroke-width="2"/></svg>Life Changing Results</h4>
  <p style="top:282px">No matter your situation, we can help. Our dietician designed meals focus on an anti-inflammatory diet, which is the foundation to good health.</p>
  <div class="btn" style="left:58px;top:346px;width:254px"><span class="dot"><svg width="14" height="14" viewBox="0 0 14 14"><path d="M2 7l3 3 7-7" fill="none" stroke="#0f4a36" stroke-width="2"/></svg></span>Check Out The Menu</div>
</div>

<!-- footer -->
<section class="abs footer"></section>
<div class="title" style="top:4874px;font-size:29px">Request <span class="accent">Catalog</span></div>
<div class="abs" style="left:373px;top:4946px;width:490px;height:42px;border-radius:21px;overflow:hidden;display:flex">
  <div style="flex:1;background:#d8d4cf;display:flex;align-items:center;padding-left:20px;font-size:13px;color:var(--ink)">Your email</div>
  <div style="width:140px;background:var(--forest);color:#fff;display:flex;align-items:center;justify-content:center;font-family:'Josefin Sans',sans-serif;font-weight:700;font-size:13px;letter-spacing:.5px">SUBSCRIBE</div>
</div>
<div class="abs" style="left:0;top:5015px;width:1200px;height:1px;background:#cfd6d2"></div>

<div class="brand" style="left:76px;top:5120px;font-size:38px">Brindle Forks</div>
<div class="abs h-font" style="left:66px;top:5196px;font-size:14px;letter-spacing:4px;color:var(--forest)">EAT BETTER. LIVE BETTER.</div>

<div class="fcol" style="left:406px"><h5>Quick Links</h5><ul><li>Home</li><li>Shop Now</li><li>About</li><li>Menu</li><li>Programs</li><li>FAQ</li></ul></div>
<div class="fcol" style="left:580px"><h5>Help&nbsp; LINKS</h5><ul><li>My Account</li><li>Site Help</li><li>Shipping</li><li>Returns</li><li>View Cart</li><li>Privacy Policy</li></ul></div>
<div class="fcol" style="left:743px;width:200px"><h5>Contact Us</h5>
  <div class="contact"><span class="ic"><svg width="12" height="14" viewBox="0 0 12 14"><path d="M6 13s5-5 5-8A5 5 0 0 0 1 5c0 3 5 8 5 8z" fill="#fff"/></svg></span><span>6055 Lorem ipsum dolor sit amet 12428</span></div>
  <div class="contact"><span class="ic"><svg width="14" height="10" viewBox="0 0 14 10"><rect x=".5" y=".5" width="13" height="9" fill="none" stroke="#fff"/><path d="M1 1l6 5 6-5" fill="none" stroke="#fff"/></svg></span><span>info@brindleforks.com</span></div>
  <div class="contact"><span class="ic"><svg width="12" height="12" viewBox="0 0 12 12"><path d="M2 1l3 1 1 3-2 1a7 7 0 0 0 3 3l1-2 3 1 0 3C5 11 1 7 2 1z" fill="#fff"/></svg></span><span>+1 888 888 8888</span></div>
  <div class="contact"><span class="ic"><svg width="14" height="14" viewBox="0 0 14 14"><circle cx="7" cy="7" r="6" fill="none" stroke="#fff" stroke-width="1.5"/><path d="M7 3v4l3 2" fill="none" stroke="#fff" stroke-width="1.5"/></svg></span><span>Hours:<br>9am - 5pm EST</span></div>
</div>
<div class="fcol" style="left:955px"><h5>Follow Us</h5><span class="social"></span><span class="social"></span><span class="social"></span><span class="social"></span></div>

<div class="abs" style="left:0;top:5332px;width:1200px;text-align:center;font-size:13.5px;color:var(--ink)">©COPYRIGHTS 2022 BRINDLEFORKS | ALL RIGHTS RESERVED</div>

</body>
</html>
```